Calm Harbor Bodywork business is seeking a Business Card Design

We are a new natural therapy business that needs a Business Card Design with an appointment card on the back.

We offer Myotherapy (muscle therapy) services and have a strong focus and commitment to helping people relieve pain and restore movement to their bodies.

I am attaching my business logo for you information.

Business card must contain my logo and have space for name, title, qualifications, phone number, email, web address

Appointment Card on the back of the card must contain space to write next appointment date, time and name of therapist and cancellation policy.

Cancellation Policy
Minimum of 24hrs notice is required prior to appointment time or full treatment fees with apply.

```html
<!DOCTYPE html>
<html lang="en">
<head>
<meta charset="utf-8">
<title>Calm Harbor Bodywork – Business &amp; Appointment Card</title>
<link href="https://fonts.googleapis.com/css2?family=Quicksand:wght@500;600;700&family=Varela+Round&display=swap" rel="stylesheet">
<style>
  :root{
    --bg:#2b2b2b;
    --card:#ffffff;
    --green:#72b236;
    --green-dark:#5f9a2a;
    --red:#c41e3a;
    --brown:#4a3b34;
    --ink:#4d4d4d;
  }
  *{box-sizing:border-box;margin:0;padding:0}
  html,body{width:1200px;height:900px;overflow:hidden;background:var(--bg)}
  body{position:relative;font-family:"Quicksand",sans-serif;color:var(--ink)}

  .card{position:absolute;width:620px;height:379px;background:var(--card);overflow:hidden;box-shadow:0 10px 30px rgba(0,0,0,.45)}

  /* Appointment side */
  .appointment-card{left:110px;top:40px;padding:34px 36px}
  .label{display:inline-block;background:var(--green);color:#fff;font-family:"Varela Round",sans-serif;font-size:17px;letter-spacing:1.5px;padding:4px 12px;text-transform:uppercase}
  .row{display:flex;align-items:flex-end;gap:10px;margin-top:18px;font-size:15px;letter-spacing:.5px;text-transform:uppercase}
  .dots{flex:1;border-bottom:2px dotted #9a9a9a;height:1px;margin-bottom:4px}
  .days{display:flex;gap:14px;margin-top:20px;font-size:15px;align-items:center}
  .day{display:flex;align-items:center;gap:6px}
  .box{width:22px;height:20px;border:2px solid var(--green);border-radius:4px;display:inline-block}
  .ampm{display:flex;gap:14px;font-size:13px;align-items:center;text-transform:uppercase}
  .policy{margin-top:22px}
  .policy p{margin-top:10px;font-size:15px;line-height:1.35;width:270px}
  .back-brand{position:absolute;right:36px;bottom:40px;display:flex;align-items:center;gap:10px;font-family:"Varela Round",sans-serif;font-size:18px;color:var(--red);white-space:nowrap}
  .back-brand .mark{width:30px;height:30px;background:var(--red);flex:none}

  /* Front side */
  .business-card{left:470px;top:480px}
  .business-card svg.panel{position:absolute;inset:0}
  .front-brand{position:absolute;left:40px;top:140px;display:flex;flex-direction:column;align-items:flex-start;gap:12px;font-family:"Varela Round",sans-serif;font-size:22px;color:var(--red);white-space:nowrap}
  .front-brand .mark{width:52px;height:52px;background:var(--red)}
  .person{position:absolute;left:360px;top:26px;text-align:center;width:230px}
  .person .name{font-family:"Varela Round",sans-serif;font-size:21px;color:var(--red);letter-spacing:.5px}
  .person .title{font-weight:700;font-size:16px;color:#fff;margin-top:2px}
  .person .qual{font-weight:600;font-size:12px;color:#fff;margin-top:2px}
  .contacts{position:absolute;left:330px;top:118px;list-style:none}
  .contacts li{display:flex;align-items:center;gap:14px;height:56px;color:#eef6e4;font-size:14px;letter-spacing:.5px;line-height:1.25}
  .icon{width:34px;height:34px;background:#fff;border:3px solid var(--red);display:flex;align-items:center;justify-content:center;flex:none}
  .icon.brown{border-color:var(--brown)}
  .icon.green{border-color:var(--green-dark)}
</style>
</head>
<body>

<section class="card appointment-card" aria-label="Appointment card">
  <span class="label">Next Appointment</span>
  <div class="row"><span>Date:</span><span class="dots"></span><span>Time:</span><span class="dots"></span>
    <span class="ampm"><span>AM</span><span class="box"></span><span>PM</span><span class="box"></span></span>
  </div>
  <div class="days">
    <span class="day">Mon <span class="box"></span></span>
    <span class="day">Tue <span class="box"></span></span>
    <span class="day">Wed <span class="box"></span></span>
    <span class="day">Thu <span class="box"></span></span>
    <span class="day">Fri <span class="box"></span></span>
    <span class="day">Sat <span class="box"></span></span>
    <span class="day">Sun <span class="box"></span></span>
  </div>
  <div class="row"><span>Name of Therapist:</span><span class="dots"></span></div>
  <div class="policy">
    <span class="label">Cancellation Policy</span>
    <p>Minimum of 24hrs notice is required prior to appointment time or full treatment fees will apply</p>
  </div>
  <div class="back-brand"><span class="mark"></span>Calm Harbor Bodywork</div>
</section>

<section class="card business-card" aria-label="Business card">
  <svg class="panel" width="620" height="379" viewBox="0 0 620 379">
    <path d="M300 0 C318 60 322 120 312 190 C302 260 300 320 310 379 L620 379 L620 0 Z" fill="var(--green)"/>
    <path d="M300 0 C318 60 322 120 312 190 C302 260 300 320 310 379" fill="none" stroke="var(--red)" stroke-width="7"/>
  </svg>

  <div class="front-brand"><span class="mark"></span>Calm Harbor Bodywork</div>

  <div class="person">
    <div class="name">Jessica Harlow</div>
    <div class="title">Myotherapist</div>
    <div class="qual">Adv. Dip. Myotherapy</div>
  </div>

  <ul class="contacts">
    <li><span class="icon"><svg width="20" height="20" viewBox="0 0 20 20"><path d="M3 6 Q10 1 17 6 L15 8 L12 7 L12 5 Q10 4 8 5 L8 7 L5 8 Z M4 10 H16 V17 H4 Z" fill="var(--red)"/></svg></span>61 3 5550 1427</li>
    <li><span class="icon brown"><svg width="20" height="16" viewBox="0 0 20 16"><rect x="1" y="1" width="18" height="14" fill="none" stroke="var(--brown)" stroke-width="2"/><path d="M1 1 L10 9 L19 1" fill="none" stroke="var(--brown)" stroke-width="2"/></svg></span>info@calmharborbodywork.com</li>
    <li><span class="icon green"><svg width="20" height="20" viewBox="0 0 20 20"><circle cx="10" cy="10" r="8" fill="none" stroke="var(--green-dark)" stroke-width="2"/><path d="M2 10 H18 M10 2 C6 6 6 14 10 18 M10 2 C14 6 14 14 10 18" fill="none" stroke="var(--green-dark)" stroke-width="1.5"/></svg></span>www.calmharborbodywork.com</li>
    <li><span class="icon"><svg width="20" height="18" viewBox="0 0 20 18"><path d="M10 1 L19 9 H16 V17 H12 V12 H8 V17 H4 V9 H1 Z" fill="var(--red)"/></svg></span>Level 2/118 Tidewater Rd,<br>Northcote VIC 3070</li>
  </ul>
</section>

</body>
</html>
```